Velk Consulting -New consulting business in architecture, urban planning, and real estate development

We need a stationery design, including logo, business cards, etc, work for a new consulting business that works in the world of architectural, urban planning and real estate development.

The name of the company is "Velk Consulting". Velk is my last name but it of course also has the meaning 'cool' and 'hip'.

Target Market(s)

The business will provide boutique consulting services to high end clients that may include property developers, cities, etc.

Industry/Entity Type

Consultant

Contact Information for Business Card

VELK Consulting
First Name Last Name
Title
Phone number
Address
Website
Optional: Twitter handle

Logo Text

VELK Consulting

Font styles to use
Sans Serif

Colors

Designer to choose colors to be used in the design.

Requirements
Must have
• Simple design
• Easy to read font
• Modern
• Elegance
• Nice font that can be used for future reports, letters, etc.
• Good colour scheme that allows for the elegance to come through
Should not have
• Complex design ideas
• Complex logos
• Not a corporate feel and look

```html
<!DOCTYPE html>
<html lang="en">
<head>
<meta charset="utf-8">
<title>Velk Consulting – Stationery Elements</title>
<link rel="stylesheet" href="https://fonts.googleapis.com/css2?family=Saira+Condensed:wght@300;400;600&family=Poppins:wght@400;500&display=swap">
<style>
  :root {
    --board: #70717b;
    --charcoal: #464648;
    --charcoal-deep: #3d3d3f;
    --lime: #c6dc3f;
    --paper: #ffffff;
    --mist: #ececec;
    --window: #dcdcde;
    --ink-soft: #8a8a8c;
    --hole: #1c1c1c;
  }
  html, body {
    margin: 0;
    padding: 0;
    width: 1200px;
    height: 1200px;
    overflow: hidden;
    background: var(--board);
  }
  .board { display: block; width: 1200px; height: 1200px; }
  .board-title { font-family: "Saira Condensed", sans-serif; fill: var(--paper); font-size: 50px; letter-spacing: 1px; }
  .board-title .strong { font-weight: 600; }
  .board-title .light { font-weight: 300; }
  .item { filter: drop-shadow(0 2px 3px rgba(0,0,0,.25)); }
  .fill-charcoal { fill: var(--charcoal); }
  .fill-deep { fill: var(--charcoal-deep); }
  .fill-lime { fill: var(--lime); }
  .fill-paper { fill: var(--paper); }
  .fill-mist { fill: var(--mist); }
  .fill-window { fill: var(--window); }
  .wordmark { font-family: "Saira Condensed", sans-serif; font-weight: 400; text-anchor: middle; letter-spacing: .4px; }
  .wordmark.on-dark { fill: var(--paper); }
  .wordmark.on-light { fill: var(--charcoal); }
  .contact { font-family: "Poppins", sans-serif; font-size: 5px; }
  .contact.on-light { fill: var(--ink-soft); }
  .contact.on-dark { fill: var(--paper); }
  .icon-light { fill: var(--ink-soft); }
  .icon-dark { fill: var(--paper); }
  .card-name { font-family: "Poppins", sans-serif; font-size: 5.5px; fill: var(--paper); letter-spacing: .6px; }
  .handle { fill: none; stroke: var(--paper); stroke-width: 5; stroke-linejoin: round; }
  .ring { fill: var(--paper); }
</style>
</head>
<body>
<svg class="board" viewBox="0 0 1000 1000" xmlns="http://www.w3.org/2000/svg">
  <defs>
    <linearGradient id="facet-tone" x1="0" y1="0" x2="1" y2="1">
      <stop offset="0" stop-color="#4a4a4c"/>
      <stop offset=".5" stop-color="#3a3a3c"/>
      <stop offset="1" stop-color="#464648"/>
    </linearGradient>
  </defs>

  <text class="board-title" x="500" y="72" text-anchor="middle"><tspan class="strong">VELK CONSULTING</tspan> <tspan class="light">STATIONERY ELEMENTS</tspan></text>

  <!-- Letterhead -->
  <g class="item letterhead">
    <rect class="fill-paper" x="66" y="110" width="260" height="368"/>
    <rect class="fill-charcoal" x="66" y="127" width="70" height="43"/>
    <rect class="fill-lime" x="96" y="134" width="9" height="9"/>
    <text class="wordmark on-dark" x="101" y="160" font-size="8">VELK CONSULTING</text>
    <polygon class="fill-charcoal" points="286,130 310,127 300,140"/>
    <polygon class="fill-lime" points="296,130 326,127 326,170"/>
    <g class="contact-block">
      <circle class="icon-light" cx="143" cy="142" r="2"/>
      <text class="contact on-light" x="149" y="144">(000) 123456789</text>
      <rect class="icon-light" x="141" y="151" width="4" height="3"/>
      <text class="contact on-light" x="149" y="154.5">info@companyname.com</text>
      <path class="icon-light" d="M143 161.5a2 2 0 1 1 0.01 0L143 165.5Z"/>
      <text class="contact on-light" x="149" y="165">Street address 123</text>
    </g>
  </g>

  <!-- Presentation folder -->
  <g class="item folder">
    <rect class="fill-paper" x="682" y="108" width="258" height="368"/>
    <polygon class="fill-charcoal" points="373,140 398,108 682,108 682,476 664,476 664,536 423,536 423,385 373,360"/>
    <polygon class="fill-lime" points="423,365 470,418 423,475"/>
    <rect class="fill-lime" x="547" y="381" width="9" height="9"/>
    <text class="wordmark on-dark" x="551" y="416" font-size="8">VELK CONSULTING</text>
    <g class="contact-block">
      <circle class="icon-dark" cx="456" cy="447" r="2.4"/>
      <text class="contact on-dark" x="462" y="449">(000) 123456789</text>
      <rect class="icon-dark" x="515" y="445" width="5" height="3.5"/>
      <text class="contact on-dark" x="524" y="449">info@companyname.com</text>
      <path class="icon-dark" d="M602 446a2.4 2.4 0 1 1 0.01 0L602 450.5Z"/>
      <text class="contact on-dark" x="609" y="449">Street address 123</text>
    </g>
    <rect class="fill-lime" x="800" y="248" width="24" height="24"/>
    <text class="wordmark on-light" x="812" y="321" font-size="17">VELK CONSULTING</text>
  </g>

  <!-- Envelope -->
  <g class="item envelope">
    <rect class="fill-paper" x="66" y="548" width="260" height="142"/>
    <rect class="fill-charcoal" x="66" y="548" width="260" height="17"/>
    <rect class="fill-charcoal" x="85" y="588" width="38" height="28"/>
    <rect class="fill-lime" x="101" y="592" width="6" height="6"/>
    <text class="wordmark on-dark" x="104" y="611" font-size="5.5">VELK CONSULTING</text>
    <polygon class="fill-lime" points="286,612 326,585 326,612"/>
    <rect class="fill-window" x="202" y="621" width="99" height="40"/>
    <g class="contact-block">
      <circle class="icon-light" cx="87" cy="636" r="2"/>
      <text class="contact on-light" x="92" y="638">(000) 123456789</text>
      <rect class="icon-light" x="85" y="645" width="4" height="3"/>
      <text class="contact on-light" x="92" y="648.5">info@companyname.com</text>
      <path class="icon-light" d="M87 656a2 2 0 1 1 0.01 0L87 660Z"/>
      <text class="contact on-light" x="92" y="659.5">Street address 123</text>
    </g>
  </g>

  <!-- CD disc and sleeve -->
  <g class="item disc">
    <circle class="fill-lime" cx="283" cy="837" r="60"/>
    <circle class="fill-window" cx="266" cy="836" r="23"/>
    <circle fill="#c4c4c6" cx="266" cy="836" r="9"/>
    <polygon class="fill-deep" points="290,836 340,810 335,868"/>
    <rect class="fill-charcoal" x="258" y="778" width="12" height="12"/>
    <text class="wordmark on-light" x="268" y="892" font-size="10">VELK CONSULTING</text>
  </g>
  <g class="item sleeve">
    <rect x="62" y="752" width="173" height="170" fill="url(#facet-tone)" role="img" aria-label="Low-poly faceted charcoal background pattern"/>
    <polygon class="fill-lime" points="62,752 122,752 62,820"/>
    <polygon class="fill-mist" points="62,800 100,922 62,922"/>
    <rect class="fill-lime" x="143" y="812" width="18" height="18"/>
    <text class="wordmark on-dark" x="153" y="856" font-size="11">VELK CONSULTING</text>
  </g>

  <!-- Shopping bag -->
  <g class="item bag">
    <path class="handle" d="M440 628 L446 576 Q448 570 454 570 L546 570 Q552 570 553 576 L558 628"/>
    <rect class="fill-charcoal" x="390" y="611" width="219" height="307"/>
    <circle fill="var(--hole)" cx="440" cy="628" r="5"/>
    <circle fill="var(--hole)" cx="558" cy="628" r="5"/>
    <rect class="fill-lime" x="486" y="676" width="28" height="28"/>
    <text class="wordmark on-dark" x="500" y="751" font-size="16">VELK CONSULTING</text>
    <polygon class="fill-lime" points="609,822 609,918 552,918"/>
  </g>

  <!-- Business cards -->
  <g class="item card-front">
    <rect class="fill-charcoal" x="679" y="531" width="150" height="83"/>
    <polygon class="fill-mist" points="812,531 829,531 829,562 800,590"/>
    <polygon class="fill-lime" points="775,614 829,560 829,614"/>
    <rect class="fill-lime" x="729" y="553" width="12" height="12"/>
    <text class="wordmark on-dark" x="735" y="587" font-size="9">VELK CONSULTING</text>
  </g>
  <g class="item card-back">
    <rect class="fill-charcoal" x="777" y="589" width="151" height="83"/>
    <polygon class="fill-lime" points="896,589 928,589 928,616"/>
    <polygon class="fill-mist" points="900,672 928,616 928,672"/>
    <text class="card-name" x="833" y="616">FULL NAME HERE</text>
    <rect class="fill-lime" x="833" y="619" width="58" height="0.7"/>
    <text class="contact on-dark" x="838" y="638">Street adress 123</text>
    <text class="contact on-dark" x="838" y="646">(000) 123456789</text>
    <text class="contact on-dark" x="831" y="654">info@companyname.com</text>
  </g>

  <!-- Spiral notebook -->
  <g class="item notebook">
    <rect x="685" y="716" width="237" height="202" fill="url(#facet-tone)" role="img" aria-label="Low-poly faceted charcoal background pattern"/>
    <polygon class="fill-mist" points="870,716 922,716 922,850 890,880"/>
    <polygon class="fill-lime" points="860,918 922,850 922,918"/>
    <g class="spiral">
      <rect class="ring" x="668" y="722" width="32" height="7" rx="3.5"/>
      <rect class="ring" x="668" y="735" width="32" height="7" rx="3.5"/>
      <rect class="ring" x="668" y="748" width="32" height="7" rx="3.5"/>
      <rect class="ring" x="668" y="761" width="32" height="7" rx="3.5"/>
      <rect class="ring" x="668" y="774" width="32" height="7" rx="3.5"/>
      <rect class="ring" x="668" y="787" width="32" height="7" rx="3.5"/>
      <rect class="ring" x="668" y="800" width="32" height="7" rx="3.5"/>
      <rect class="ring" x="668" y="813" width="32" height="7" rx="3.5"/>
      <rect class="ring" x="668" y="826" width="32" height="7" rx="3.5"/>
      <rect class="ring" x="668" y="839" width="32" height="7" rx="3.5"/>
      <rect class="ring" x="668" y="852" width="32" height="7" rx="3.5"/>
      <rect class="ring" x="668" y="865" width="32" height="7" rx="3.5"/>
      <rect class="ring" x="668" y="878" width="32" height="7" rx="3.5"/>
      <rect class="ring" x="668" y="891" width="32" height="7" rx="3.5"/>
      <rect class="ring" x="668" y="904" width="32" height="7" rx="3.5"/>
    </g>
    <rect class="fill-lime" x="782" y="786" width="22" height="22"/>
    <text class="wordmark on-dark" x="793" y="832" font-size="13">VELK CONSULTING</text>
  </g>
</svg>
</body>
</html>
```